BOLD & MINIMALIST DESIGN NEEDED

We want a very bold but minimalistic business card design that is impactful and utilizes both sides of the business card. Our current logo is included for your use.

We want bold fonts and good use of negative space. We don't want the logo to overpower the design.

Target Market(s)

Professionals who are building new commercial buildings.

Industry/Entity Type

Construction

Contact Information for Business Card

Name, Title, email, office phone, cell phone, website

Font styles to use
Serif
Sans Serif

Requirements
Must have
• Bold design!

```html
<!DOCTYPE html>
<html lang="en">
<head>
<meta charset="utf-8">
<title>Ridgeline Design + Build — Business Card</title>
<link href="https://fonts.googleapis.com/css2?family=Montserrat:wght@400;500;700;800&display=swap" rel="stylesheet">
<style>
  :root {
    --stage: #3c3c3e;
    --card: #1e1e1f;
    --card-edge: #2a2a2c;
    --green: #7dc242;
    --white: #f4f4f4;
    --muted: #4a4a4c;
  }
  * { box-sizing: border-box; margin: 0; padding: 0; }
  html, body {
    width: 1200px; height: 875px; overflow: hidden;
    background: var(--stage);
    font-family: "Montserrat", sans-serif;
  }
  .stage {
    width: 1200px; height: 875px;
    display: flex; align-items: center; justify-content: center; gap: 40px;
  }
  .card {
    position: relative;
    width: 540px; height: 309px;
    background: var(--card);
    border-radius: 18px;
    box-shadow: 0 18px 40px rgba(0,0,0,.45), inset 0 0 0 1px var(--card-edge);
    overflow: hidden;
  }

  /* Front side */
  .card--front { display: flex; align-items: center; justify-content: center; }
  .brand { display: flex; align-items: center; gap: 16px; }
  .brand__mark { width: 34px; height: 34px; background: var(--green); }
  .brand__name {
    font-weight: 800; text-transform: uppercase; line-height: 1;
    color: var(--muted);
  }
  .card--front .brand__name { font-size: 46px; letter-spacing: .5px; }
  .brand__tag {
    display: block; font-size: 15px; letter-spacing: 7px; margin-top: 8px;
  }

  /* Back side */
  .card--back { padding: 44px 0 0 46px; }
  .card--back .brand__name { color: var(--white); font-size: 32px; }
  .card--back .brand__tag { font-size: 11px; letter-spacing: 5px; margin-top: 6px; }
  .person { display: flex; gap: 14px; margin-top: 34px; }
  .person__bar { width: 14px; height: 50px; background: var(--green); margin-top: 4px; }
  .person__name { color: var(--green); font-weight: 700; font-size: 26px; line-height: 1.1; letter-spacing: .5px; }
  .person__title { color: var(--white); font-weight: 500; font-size: 14px; margin-top: 2px; }
  .contacts { list-style: none; margin: 16px 0 0 30px; }
  .contacts li {
    display: flex; align-items: center; gap: 10px;
    color: var(--white); font-size: 14px; font-weight: 500; line-height: 1.65;
  }
  .contacts svg { width: 12px; height: 12px; fill: var(--green); flex: none; }
  .contacts .accent { color: var(--green); }
</style>
</head>
<body>
<main class="stage">
  <section class="card card--front" aria-label="Card front">
    <div class="brand">
      <span class="brand__mark"></span>
      <span class="brand__name">Ridgeline<span class="brand__tag">Design + Build</span></span>
    </div>
  </section>

  <section class="card card--back" aria-label="Card back">
    <div class="brand">
      <span class="brand__name">Ridgeline<span class="brand__tag">Design + Build</span></span>
    </div>
    <div class="person">
      <span class="person__bar"></span>
      <div>
        <p class="person__name">DORIAN VALE</p>
        <p class="person__title">Owner/CEO</p>
      </div>
    </div>
    <ul class="contacts">
      <li><svg viewBox="0 0 24 24"><path d="M6.6 10.8a15.1 15.1 0 0 0 6.6 6.6l2.2-2.2c.3-.3.7-.4 1-.2 1.1.4 2.3.6 3.6.6.6 0 1 .4 1 1V20c0 .6-.4 1-1 1A17 17 0 0 1 3 4c0-.6.4-1 1-1h3.5c.6 0 1 .4 1 1 0 1.3.2 2.5.6 3.6.1.3 0 .7-.2 1z"/></svg>07 5550 2100</li>
      <li><svg viewBox="0 0 24 24"><path d="M7 1h10a2 2 0 0 1 2 2v18a2 2 0 0 1-2 2H7a2 2 0 0 1-2-2V3a2 2 0 0 1 2-2zm0 3v14h10V4z"/></svg>0400 555 217</li>
      <li><svg viewBox="0 0 24 24"><path d="M2 5h20v14H2zm2 2v.5l8 5 8-5V7l-8 5z"/></svg>info@ridgelinebuild.com</li>
      <li><svg viewBox="0 0 24 24"><circle cx="12" cy="12" r="10"/></svg><span>www.<span class="accent">ridgelinebuild</span>.com</span></li>
    </ul>
  </section>
</main>
</body>
</html>
```